Clean Vexlo Ads Banner Design For A Finance Company

Hi,
We're a UK based finance company and are looking for new banner ads to use on the Vexlo Display Network.
We want the end product to stand out by using strong, minimal design - ideally starting from a dark theme, although I'm open to ideas.
The copy should read:
'Fast Bridging Loans From 0.39% PM'
Once we have these designs agreed, we are looking to replicate them for other products, changing only the text on each ad - for example, 'commercial mortgage service you can rely on' or 'development finance service you can rely on'.
The colours used on our website are the following:
Black - #040303
Orange - #f79124
White - #ffffff
Grey - #ffffff
Example ads that I like - https://www.plimrake.com/wp-content/uploads/2021/07/vexlo-display-ads-example-2-final.png.webp
2 - https://qarnelvistahub.com/wp-content/uploads/2020/03/fbdd56ba3bd16c7a8debb13a411de786.jpg

```html
<!DOCTYPE html>
<html lang="en">
<head>
<meta charset="utf-8">
<title>Fast Bridging Loans – Korvane Finance Limited</title>
<link rel="stylesheet" href="https://fonts.googleapis.com/css2?family=Playfair+Display:wght@700;900&display=swap">
<style>
  :root {
    --orange: #f79124;
    --orange-light: #fab56b;
    --pattern-tint: #f9a951;
    --stripe-tint: #fbc891;
    --white: #ffffff;
    --black: #040303;
    --photo-top: #4a3126;
    --photo-mid: #c98f76;
    --photo-low: #f3c3b4;
  }
  html, body {
    margin: 0;
    padding: 0;
    overflow: hidden;
    background: var(--white);
  }
  .banner {
    position: relative;
    width: 1200px;
    height: 2398px;
    overflow: hidden;
    background: var(--orange);
    font-family: "Playfair Display", Georgia, serif;
    font-variant-numeric: lining-nums;
    color: var(--white);
  }
  .backdrop {
    position: absolute;
    left: 0;
    top: 0;
    display: block;
  }
  .headline {
    position: absolute;
    left: 76px;
    top: 136px;
    margin: 0;
    font-weight: 900;
    font-size: 182px;
    line-height: 172px;
    letter-spacing: 11px;
    white-space: nowrap;
  }
  .rate-from {
    position: absolute;
    left: 78px;
    top: 698px;
    margin: 0;
    font-weight: 900;
    font-size: 83px;
    line-height: 83px;
    letter-spacing: 5px;
  }
  .rate-value {
    position: absolute;
    left: 76px;
    top: 764px;
    margin: 0;
    font-weight: 900;
    font-size: 212px;
    line-height: 212px;
    letter-spacing: 4px;
    white-space: nowrap;
  }
  .rate-unit {
    font-size: 80px;
    letter-spacing: 1px;
  }
  .pattern-block {
    position: absolute;
    left: 96px;
    top: 1050px;
    width: 272px;
    height: 452px;
    background: var(--pattern-tint);
  }
  .stripe-block {
    position: absolute;
    left: 0;
    top: 1830px;
    width: 240px;
    height: 568px;
    border-radius: 0 120px 0 0;
    background: var(--stripe-tint);
  }
  .portrait {
    position: absolute;
    left: 268px;
    top: 1016px;
    width: 900px;
    height: 1382px;
    border-radius: 450px 450px 0 0;
    background: linear-gradient(180deg, var(--photo-top) 0%, var(--photo-mid) 45%, var(--photo-low) 100%);
  }
  .brand-panel {
    position: absolute;
    left: 330px;
    top: 1927px;
    width: 800px;
    height: 471px;
    background: var(--white);
    border-radius: 18px 18px 0 0;
    display: flex;
    flex-direction: column;
    align-items: center;
    justify-content: center;
  }
  .brand-name {
    margin: 0;
    color: var(--orange);
    font-weight: 900;
    font-size: 140px;
    line-height: 1;
  }
  .brand-sub {
    margin: 22px 0 0;
    color: var(--orange);
    font-weight: 900;
    font-size: 60px;
    line-height: 1;
  }
</style>
</head>
<body>
<div class="banner">
  <svg class="backdrop" width="1200" height="2398" viewBox="0 0 1200 2398" aria-hidden="true">
    <polygon points="700,0 1200,0 1200,1917" fill="var(--orange-light)"/>
    <polygon points="1200,575 1045,1150 1200,1725" fill="var(--white)"/>
  </svg>

  <h1 class="headline">FAST<br>BRIDGING<br>LOANS</h1>
  <p class="rate-from">FROM</p>
  <p class="rate-value">0.39%<span class="rate-unit">PM</span></p>

  <div class="pattern-block" role="img" aria-label="Decorative grid of small pale dots"></div>
  <div class="stripe-block" role="img" aria-label="Decorative rounded block of white horizontal stripes"></div>

  <div class="portrait" role="img" aria-label="Photo of a smiling woman with long dark hair in a pink top, sitting behind a white laptop"></div>

  <div class="brand-panel">
    <p class="brand-name">Korvane</p>
    <p class="brand-sub">Finance Limited</p>
  </div>
</div>
</body>
</html>
```